Provide bookkeeping and accounting services to small and growing businesses

We need website and logo design using the name Dornaby as the logo.
The target audience are small companies and startups who need:
1) Simple bookkeeping services
2) Accounting advice that only someone with many years of senior financial experience as a CPA can provide.

The services are provided by two individuals. each of whom specialize in one of the areas.

We want the website to be clean without a lot of visual distraction but don't know how to make a boring subject interesting. We believe our potential clients, small business owners, need to find what they want quickly and easily without a lot of verbiage or distractions.

We've attached a draft of the homepage and have completed the text on most of the other pages.

Target Market(s)

small and early stage growth companies in San Diego North County

Industry/Entity Type

Accounting

Number of Pages Required

1 page

Font styles to use
Sans Serif

Colors
86cfc6
33b8a4
85cae6

Requirements
Must have
• We need a design for the website homepage that includes the name Dornaby as the logo. Must include a design for the name.
• Must have color in teal or greenish blue.
Nice to have
• White background, clean, clear, uncluttered.
• We would like to use the design in a Theme on a WordPress website. Themes Paper Lantern and Quiet Harbour are appealing to us.
Should not have
• Moving pictures

```html
<!DOCTYPE html>
<html lang="en">
<head>
<meta charset="utf-8">
<title>Dornaby Accounting &amp; Bookkeeping</title>
<link href="https://fonts.googleapis.com/css2?family=Lato:wght@300;400;700&display=swap" rel="stylesheet">
<style>
:root{
  --teal:#33b8a4;
  --teal-soft:#86cfc6;
  --sky:#85cae6;
  --deep:#0f4a4e;
  --deep-2:#135a5c;
  --ink:#3d4548;
  --muted:#7c8589;
  --line:#dfe4e5;
  --nav:#e9ecec;
  --foot:#f1f3f3;
  --white:#ffffff;
}
*{box-sizing:border-box;margin:0;padding:0}
html,body{width:668px;height:1200px;overflow:hidden;background:var(--white)}
body{font-family:"Lato",Arial,sans-serif;color:var(--ink);font-size:8px;line-height:1.45}
.page{width:668px;height:1200px;position:relative;overflow:hidden}

/* header */
.site-header{height:62px;display:flex;align-items:center;justify-content:space-between;padding:0 38px}
.brand{display:flex;align-items:center;gap:8px}
.brand-name{font-size:15px;font-weight:700;color:var(--teal);letter-spacing:.5px}
.brand-tag{font-size:9px;font-weight:700;color:var(--ink);line-height:1.25;padding-left:10px;border-left:1px solid var(--line);margin-left:4px}
.contact-bar{display:flex;gap:16px;align-items:center;font-size:8px;color:var(--muted)}
.contact-bar span{display:flex;align-items:center;gap:5px}
.ico{width:14px;height:14px;border:1px solid var(--teal);border-radius:50%;display:inline-flex;align-items:center;justify-content:center}

/* nav */
.main-nav{height:22px;background:var(--nav);display:flex;padding-left:38px}
.main-nav a{font-size:7.5px;color:var(--ink);text-decoration:none;padding:0 9px;line-height:22px;letter-spacing:.3px}
.main-nav a.active{background:var(--white)}

/* hero */
.hero{height:271px;position:relative;background:linear-gradient(160deg,#5d6461 0%,#8c8a80 40%,#b8b3a6 65%,#6e716c 100%);display:flex;align-items:center;justify-content:center}
.hero::after{content:"";position:absolute;inset:0;background:rgba(25,35,38,.35)}
.hero h1{position:relative;z-index:1;color:var(--white);font-weight:300;text-align:center;font-size:23px;line-height:1.25;letter-spacing:.5px;text-transform:uppercase}

/* welcome */
.welcome{display:flex;padding:18px 38px 0;height:290px;gap:18px}
.welcome-main{flex:1}
.welcome-head{display:flex;align-items:center;gap:10px;margin-bottom:14px}
.round-ico{width:30px;height:30px;border:2px solid var(--teal);border-radius:50%;flex:none;display:flex;align-items:center;justify-content:center}
.welcome-head h2{font-size:12px;font-weight:700;line-height:1.25;text-transform:uppercase;color:var(--ink)}
.welcome-body{display:flex;gap:14px}
.portrait{width:178px;height:178px;flex:none;background:linear-gradient(180deg,#b7bcbd,#8a9191 60%,#5f6768)}
.welcome-text p{font-size:7.5px;color:var(--muted);margin-bottom:9px}
.btn-outline{display:inline-block;border:1px solid var(--teal);color:var(--teal);font-size:6.5px;padding:3px 7px;text-transform:uppercase;letter-spacing:.3px}
.consult{width:162px;border:4px solid var(--teal-soft);padding:10px 10px;height:228px;margin-top:2px}
.consult-head{display:flex;gap:8px;align-items:center;margin-bottom:10px}
.consult-head h3{font-size:11px;font-weight:400;color:var(--teal);line-height:1.2;text-transform:uppercase}
.field{border:1px solid var(--line);height:15px;font-size:6.5px;color:var(--muted);padding:3px 5px;margin-bottom:6px}
.field.tall{height:36px}
.btn-fill{display:inline-block;background:var(--teal);color:var(--white);font-size:6.5px;padding:4px 8px;text-transform:uppercase}

/* services */
.services{display:flex;height:210px}
.service{flex:1;padding:24px 30px 0 52px;color:var(--white)}
.service.accounting{background:var(--deep)}
.service.bookkeeping{background:var(--deep-2)}
.service-head{display:flex;align-items:center;gap:10px;margin-bottom:12px}
.service-head .round-ico{border-color:var(--white)}
.service-head h3{font-size:12px;font-weight:400;line-height:1.2;text-transform:uppercase}
.service ul{list-style:none;margin-bottom:12px}
.service li{font-size:7.5px;margin-bottom:4px;display:flex;align-items:center;gap:6px}
.service li::before{content:"";width:5px;height:5px;border-radius:50%;background:var(--teal-soft)}
.service .btn-outline{border-color:var(--white);color:var(--white)}

/* stories */
.stories{display:flex;padding:22px 38px 0;height:200px;gap:24px}
.stories-main{flex:1}
.stories h2{font-size:12px;font-weight:700;text-transform:uppercase;margin-bottom:10px}
.quote{display:flex;gap:8px}
.quote-mark{color:var(--teal);font-size:22px;line-height:1}
.quote p{font-size:7.5px;color:var(--muted)}
.quote-name{color:var(--teal);font-size:8px;margin-top:8px}
.quote-role{font-size:6.5px;color:var(--muted)}
.subscribe{width:170px;background:var(--sky);padding:10px 12px;height:108px}
.subscribe h3{color:var(--white);font-size:11px;font-weight:400;text-transform:uppercase;margin-bottom:8px}
.subscribe .field{background:var(--white);border:none}

/* footer */
.site-footer{position:absolute;left:0;right:0;bottom:0;height:137px;background:var(--foot);padding:14px 38px 0;display:flex;gap:38px}
.foot-col h4{font-size:8px;font-weight:700;margin-bottom:7px}
.foot-col li{list-style:none;font-size:7px;color:var(--muted);margin-bottom:3px;display:flex;align-items:center;gap:5px}
.sq{width:11px;height:11px;background:var(--teal-soft);flex:none}
.foot-brand{margin-left:auto;text-align:left}
.foot-brand .brand{margin-bottom:10px;margin-top:16px}
.foot-brand p{font-size:6.5px;color:var(--muted)}
</style>
</head>
<body>
<div class="page">

<header class="site-header">
  <div class="brand">
    <span class="brand-name">DORNABY</span>
    <span class="brand-tag">ACCOUNTING &amp;<br>BOOKKEEPING</span>
  </div>
  <div class="contact-bar">
    <span><i class="ico"><svg width="7" height="7" viewBox="0 0 10 10"><path d="M2 1l2 2-1 1.5c.6 1.2 1.3 1.9 2.5 2.5L7 6l2 2-1.5 1.5C4 9 1 6 .5 2.5z" fill="#33b8a4"/></svg></i>(760) 555 0142</span>
    <span><i class="ico"><svg width="8" height="6" viewBox="0 0 10 7"><rect x=".5" y=".5" width="9" height="6" fill="none" stroke="#33b8a4"/><path d="M.5.5L5 4l4.5-3.5" fill="none" stroke="#33b8a4"/></svg></i>hello@dornaby.com</span>
  </div>
</header>

<nav class="main-nav">
  <a class="active">HOME</a><a>ABOUT US</a><a>SERVICES</a><a>EXPERIENCE</a><a>RESOURCES</a><a>CONTACT US</a>
</nav>

<section class="hero" role="img" aria-label="Desk with calculator, paperwork and laptop">
  <h1>We provide a full range of<br>accounting and bookkeeping services</h1>
</section>

<section class="welcome">
  <div class="welcome-main">
    <div class="welcome-head">
      <span class="round-ico"><svg width="14" height="14" viewBox="0 0 14 14"><rect x="2" y="3" width="10" height="8" fill="none" stroke="#33b8a4" stroke-width="1.4"/><path d="M4 6h6M4 8h4" stroke="#33b8a4"/></svg></span>
      <h2>Welcome to Dornaby<br>Accounting &amp; Bookkeeping</h2>
    </div>
    <div class="welcome-body">
      <div class="portrait" role="img" aria-label="Portrait of an accountant in a shirt and glasses"></div>
      <div class="welcome-text">
        <p>Dornaby offers a flexible range of accounting and bookkeeping services and support for small and growing organizations of San Diego North County.</p>
        <p>We provide bookkeeping services specializing in cloud software in your offices or remotely from ours. We also provide a broad range of accounting services or financial advice.</p>
        <span class="btn-outline">Learn more</span>
      </div>
    </div>
  </div>
  <aside class="consult">
    <div class="consult-head">
      <span class="round-ico"><svg width="14" height="14" viewBox="0 0 14 14"><rect x="3" y="2" width="8" height="10" fill="none" stroke="#33b8a4" stroke-width="1.4"/><path d="M5 5h4M5 7h4M5 9h3" stroke="#33b8a4"/></svg></span>
      <h3>Request a<br>free consultation</h3>
    </div>
    <div class="field">Full Name</div>
    <div class="field">Email Address</div>
    <div class="field">Company Name</div>
    <div class="field">Phone</div>
    <div class="field tall">Anything else we should know in advance?</div>
    <span class="btn-fill">Submit</span>
  </aside>
</section>

<section class="services">
  <div class="service accounting">
    <div class="service-head">
      <span class="round-ico"><svg width="14" height="14" viewBox="0 0 14 14"><rect x="3" y="2" width="8" height="10" fill="none" stroke="#fff" stroke-width="1.3"/><path d="M5 5h4M5 7h1M8 7h1M5 9h1M8 9h1" stroke="#fff"/></svg></span>
      <h3>Accounting<br>services</h3>
    </div>
    <ul>
      <li>Accounts payable</li>
      <li>Billing and accounts receivable</li>
      <li>Financial statement preparation</li>
      <li>Payroll services</li>
      <li>Daily deposit verification</li>
    </ul>
    <span class="btn-outline">Learn more</span>
  </div>
  <div class="service bookkeeping">
    <div class="service-head">
      <span class="round-ico"><svg width="14" height="14" viewBox="0 0 14 14"><path d="M2 3h4.5v9H2zM7.5 3H12v9H7.5z" fill="none" stroke="#fff" stroke-width="1.3"/></svg></span>
      <h3>Bookkeeping<br>services</h3>
    </div>
    <ul>
      <li>Bank Reconciliation Reports</li>
      <li>Budgeting Cash Flow Statement</li>
      <li>Create Collection Process</li>
      <li>Record Payments</li>
      <li>Financial Dashboard</li>
    </ul>
    <span class="btn-outline">Learn more</span>
  </div>
</section>

<section class="stories">
  <div class="stories-main">
    <h2>Featured success stories</h2>
    <div class="quote">
      <span class="quote-mark">&ldquo;</span>
      <div>
        <p>Working with this team changed how we run our books. Every month closes on time, reports are clear, and we finally understand our cash flow. Their advice helped us plan hiring, manage growth and stay ready for tax season without stress. We recommend them to any owner who wants calm, reliable numbers.</p>
        <div class="quote-name">&ndash; Mark Ellison</div>
        <div class="quote-role">Founder, local startup</div>
      </div>
    </div>
  </div>
  <aside class="subscribe">
    <h3>Subscribe newsletter</h3>
    <div class="field">Name</div>
    <div class="field">Email Address</div>
    <span class="btn-fill">Join</span>
  </aside>
</section>

<footer class="site-footer">
  <div class="foot-col">
    <h4>Quick Links</h4>
    <ul><li>Home</li><li>About Us</li><li>Services</li><li>Experience</li><li>Resources</li><li>Contact Us</li></ul>
  </div>
  <div class="foot-col">
    <h4>Get in Touch</h4>
    <ul>
      <li><span class="sq"></span>48 Harbour View Lane<br>Oceanside, CA 92054</li>
      <li><span class="sq"></span>(760) 555 0142</li>
      <li><span class="sq"></span>hello@dornaby.com</li>
    </ul>
  </div>
  <div class="foot-col">
    <h4>Connect With Us</h4>
    <ul>
      <li><span class="sq"></span>Social Page</li>
      <li><span class="sq"></span>News Feed</li>
      <li><span class="sq"></span>Pro Network</li>
    </ul>
  </div>
  <div class="foot-brand">
    <div class="brand">
      <span class="brand-name">DORNABY</span>
      <span class="brand-tag">ACCOUNTING &amp;<br>BOOKKEEPING</span>
    </div>
    <p>&copy; 2016 Dornaby Accounting &amp; Bookkeeping<br>Privacy Policy | Terms of Use | Sitemap</p>
  </div>
</footer>

</div>
</body>
</html>
```